Onsite Energy for Retail Tenants

Need a short one page-3 part build showing how the program for discounted clean energy works - moving into a call to action with multiple links.

1) Solar Garden Produces Energy
2) Credits Available for Tenants’ Utility Bills
3) Sign Up to Receive Utility Bill Credits.
Save 5%

This document will be used:
1) Embedded in Mailchimp emails
2) as an html landing page
3) as an image

Use the latest powerpoint Tenant slide E as guidance
Updates

Infographic is simplistic. 3 part build using graphics and information. Flow is really important so Gifs welcome.

Target Market(s)

Owners of small stores throughout the US.

Industry/Entity Type

Real Estate

Colors

Designer to choose colors to be used in the design.

Requirements
Must have
• It must explain the program clearly and succinctly using the language from the first slide of Mockup 1. This slide must become an elegant build for the 3 step process. See Mockup 2 for its cleanliness ideas for a similar but different program.
• The second slide of mockup 1 is the call to action and must have clickable links and promote trust.
• Please use the attached font styles.
• The text is sparse and so needs to be bold and in order and with the graphics needs to explain how it works perfectly.
• The graphics should be clean and sophisticated but the message and flow needs to be simple.
Nice to have
• Moving arrows to show flow of energy and credits.
• Ability to switch out language of text.

```html
<!DOCTYPE html>
<html lang="en">
<head>
<meta charset="utf-8">
<title>How the Program for Discounted Clean Energy Works</title>
<link rel="stylesheet" href="https://fonts.googleapis.com/css2?family=Varela+Round&family=Fira+Sans+Extra+Condensed:wght@600&family=Open+Sans:ital,wght@0,400;0,700;1,400;1,600&display=swap">
<style>
  :root {
    --blue-title: #1f72b8;
    --blue-text: #1f6fb5;
    --blue-panel: #2a9fd8;
    --green: #3bb34a;
    --grey-line: #6d6e71;
    --grey-dash: #b9b9b9;
    --grey-step: #666666;
    --ink: #222222;
    --sun: #f9e43a;
    --wall: #f26a2e;
    --wall-light: #fbc97a;
    --pole: #2f3a48;
  }
  * { box-sizing: border-box; margin: 0; padding: 0; }
  html, body { width: 1200px; height: 720px; overflow: hidden; background: #ffffff; }
  body { font-family: "Open Sans", sans-serif; color: var(--ink); }
  .canvas { position: relative; width: 1200px; height: 720px; }
  .abs { position: absolute; white-space: nowrap; }

  .page-title {
    left: 0; top: 18px; width: 1200px; text-align: center;
    font-family: "Varela Round", sans-serif; font-size: 36px; color: var(--blue-title);
  }
  .title-rule { left: 86px; top: 71px; width: 1060px; height: 2px; background: var(--blue-title); }

  .flow-lines { left: 0; top: 0; }

  .house-illustration {
    left: 40px; top: 96px; width: 515px; height: 530px;
    border-radius: 30px;
    background: linear-gradient(150deg, var(--sun) 0%, var(--wall-light) 40%, var(--wall) 100%);
  }
  .utility-pole {
    left: 612px; top: 308px; width: 14px; height: 144px;
    background: var(--pole); border-radius: 3px;
  }

  .panels-label {
    left: 141px; top: 158px;
    font-family: "Fira Sans Extra Condensed", sans-serif; font-weight: 600;
    font-size: 34px; color: var(--blue-panel);
  }
  .tenant-label {
    font-family: "Fira Sans Extra Condensed", sans-serif; font-weight: 600;
    font-size: 24px; color: var(--ink); transform: rotate(-28deg);
  }
  .tenant-two { left: 224px; top: 390px; }
  .tenant-one { left: 230px; top: 548px; }

  .garden-caption {
    left: 359px; top: 132px;
    font-style: italic; font-size: 17px; line-height: 22px; color: var(--blue-text);
  }

  .step-heading {
    font-family: "Varela Round", sans-serif; font-size: 37px; color: var(--grey-step);
    background: #ffffff; padding: 0 4px; line-height: 1;
  }
  .step-one-heading { left: 666px; top: 170px; }
  .step-two-heading { left: 721px; top: 460px; }

  .body-text { font-size: 13.5px; line-height: 17.5px; color: var(--ink); }
  .discount-agreement { left: 728px; top: 225px; }
  .receive-credits { left: 878px; top: 252px; }
  .tenant-credits {
    left: 884px; top: 308px;
    font-style: italic; font-weight: 600; font-size: 11px; line-height: 14px; color: var(--blue-text);
  }
  .dollar-mark { left: 804px; top: 262px; font-family: "Varela Round", sans-serif; font-size: 38px; line-height: 1; color: var(--green); }
  .save-rate { left: 734px; top: 305px; font-family: "Varela Round", sans-serif; font-size: 22px; line-height: 1; color: var(--green); }

  .phone-hand {
    left: 836px; top: 260px; width: 34px; height: 104px; border-radius: 8px;
    background: linear-gradient(180deg, #2b90d9 0%, #f4b184 70%, #222 100%);
  }
  .lease-note {
    left: 700px; top: 366px; width: 290px; text-align: center;
    font-style: italic; font-size: 11.5px; color: var(--blue-text);
  }
  .guarantee-pill {
    left: 754px; top: 382px; width: 180px; height: 20px; border-radius: 10px;
    background: var(--green); color: #fff; text-align: center;
    font-style: italic; font-size: 11.5px; line-height: 20px;
  }

  .provide-info { left: 711px; top: 507px; }
  .connect-options { left: 711px; top: 571px; font-weight: 700; font-size: 11px; line-height: 16px; }
  .or-word { left: 794px; top: 572px; font-family: "Varela Round", sans-serif; font-size: 34px; line-height: 1; color: var(--ink); }
  .form-caption { left: 842px; top: 618px; font-size: 12px; }

  .data-use { left: 999px; top: 420px; }

  .logo-slot { left: 14px; top: 668px; font-family: "Open Sans", sans-serif; font-weight: 700; font-size: 26px; color: #000; }
</style>
</head>
<body>
<main class="canvas">
  <h1 class="abs page-title">How the Program for Discounted Clean Energy Works?</h1>
  <div class="abs title-rule"></div>

  <div class="abs house-illustration" role="img" aria-label="Illustration of a sunny sky and a two-tenant orange building with rooftop solar panels"></div>
  <div class="abs utility-pole" role="img" aria-label="Illustration of a utility pole with power lines"></div>

  <svg class="abs flow-lines" width="1200" height="720" viewBox="0 0 1200 720" aria-hidden="true">
    <g fill="none" stroke="var(--grey-line)" stroke-width="3">
      <polyline points="160,264 160,206 618,206 618,296"/>
      <line x1="402" y1="206" x2="402" y2="260"/>
      <polyline points="282,578 690,578 690,298"/>
      <line x1="780" y1="408" x2="780" y2="462"/>
      <polyline points="918,568 940,568 940,456 986,456"/>
      <polyline points="608,284 618,298 628,284"/>
      <polyline points="680,310 690,296 700,310"/>
      <polyline points="770,450 780,464 790,450"/>
      <polyline points="974,446 988,456 974,466"/>
    </g>
    <g fill="none" stroke="var(--grey-dash)" stroke-width="1.5" stroke-dasharray="7 5">
      <rect x="644" y="188" width="372" height="220" rx="36"/>
      <rect x="702" y="474" width="216" height="180" rx="32"/>
    </g>
    <g>
      <rect x="656" y="224" width="66" height="66" rx="5" fill="#dfe6ee"/>
      <rect x="656" y="224" width="66" height="12" rx="3" fill="#4a5866"/>
      <circle cx="689" cy="258" r="14" fill="#2a9fd8"/>
      <circle cx="689" cy="253" r="5" fill="#fff"/>
      <path d="M680 266 a9 7 0 0 1 18 0" fill="#fff"/>
      <rect x="670" y="276" width="16" height="8" rx="1" fill="#4a5866"/>
      <rect x="690" y="276" width="18" height="8" rx="1" fill="var(--green)"/>
    </g>
    <g fill="none" stroke="#222" stroke-width="2">
      <rect x="852" y="570" width="34" height="44" rx="3"/>
      <rect x="862" y="566" width="14" height="7" rx="2" fill="#fff"/>
      <line x1="858" y1="584" x2="878" y2="584"/>
      <line x1="858" y1="592" x2="878" y2="592"/>
      <line x1="858" y1="600" x2="870" y2="600"/>
      <line x1="874" y1="606" x2="892" y2="584"/>
    </g>
  </svg>

  <div class="abs panels-label">Solar Panels</div>
  <div class="abs tenant-label tenant-two">Tenant 2</div>
  <div class="abs tenant-label tenant-one">Tenant 1</div>

  <p class="abs garden-caption">Solar Garden Produces<br>Energy and Property<br>receives Utility Credits</p>

  <h2 class="abs step-heading step-one-heading">Step 1</h2>
  <p class="abs body-text discount-agreement">Sign Up for the<br>Electricity Discount<br>Agreement.</p>
  <div class="abs dollar-mark">$</div>
  <div class="abs save-rate">Save 5%</div>
  <div class="abs phone-hand" role="img" aria-label="Illustration of a hand holding a smartphone showing a utility bill"></div>
  <p class="abs body-text receive-credits">Sign Up to Receive<br>Credits on your<br>Utility Bill</p>
  <p class="abs tenant-credits">Credits Available<br>for Tenants’ Utility Bills</p>
  <p class="abs lease-note">It runs only for as long as you lease.</p>
  <div class="abs guarantee-pill">Your Discount is Guaranteed</div>

  <h2 class="abs step-heading step-two-heading">Step 2</h2>
  <p class="abs body-text provide-info">Securely Provide Brightfield<br>Solar with your Utility<br>information through MeterLink</p>
  <p class="abs connect-options">MeterLink<br>Valo online<br>account</p>
  <div class="abs or-word">or</div>
  <p class="abs form-caption">Valo form</p>

  <p class="abs body-text data-use">We use the information<br>only to credit your bill,<br>generate your invoice,<br>and provide clean<br>discounted energy.</p>

  <div class="abs logo-slot">Your Logo Here.....</div>
</main>
</body>
</html>
```